Business Card Design for a Personal Trainer

I need a business card design for my job as a personal trainer. It should have a unique, modern and exclusive design. On the front there should be only my logo with my name and my job. 0162/3819204 Tobias Lendhart Wiesengrundweg 14 80417 Munich Germany The most important contact information is the web adress. it can be bigger than the rest, but its not necessary. The card should be 8,5cmx5,5cm big. Font: Roboto. Colors: black, white, gray, 56c1ff.

```html
<!DOCTYPE html>
<html lang="de">
<head>
<meta charset="utf-8">
<title>Tobias Lendhart – Personal Trainer Business Card</title>
<link rel="stylesheet" href="https://fonts.googleapis.com/css2?family=Roboto:ital,wght@0,300;0,400;0,500;1,700;1,900&display=swap">
<style>
  :root {
    --page-bg: #e6e8eb;
    --card-light: #f5f5f5;
    --card-mid: #dedede;
    --card-dark: #c4c4c4;
    --ink: #111111;
    --ink-soft: #2b2b2b;
    --rule: #3a3a3a;
    --swoosh-black: #111111;
    --photo-light: #9c9c9c;
    --photo-dark: #2e2e2e;
  }
  * { box-sizing: border-box; margin: 0; padding: 0; }
  html, body {
    width: 1200px;
    height: 970px;
    overflow: hidden;
    background: var(--page-bg);
    font-family: "Roboto", Arial, sans-serif;
  }
  .canvas {
    position: relative;
    width: 1200px;
    height: 970px;
  }
  .card {
    position: absolute;
    left: 100px;
    top: 161px;
    width: 1000px;
    height: 647px;
    border-radius: 30px;
    overflow: hidden;
    background: linear-gradient(160deg, var(--card-light) 0%, var(--card-mid) 55%, var(--card-dark) 100%);
    box-shadow: 0 18px 40px rgba(0,0,0,0.18);
  }
  .card__swoosh {
    position: absolute;
    left: 0;
    top: 0;
    width: 1000px;
    height: 647px;
  }
  .card__portrait {
    position: absolute;
    left: 24px;
    top: 64px;
    width: 396px;
    height: 540px;
    border-radius: 110px 110px 0 0;
    background: radial-gradient(ellipse at 50% 30%, var(--photo-light) 0%, var(--photo-dark) 75%);
  }
  .card__name {
    position: absolute;
    left: 445px;
    top: 102px;
    width: 505px;
    text-align: center;
    font-weight: 400;
    font-size: 53px;
    line-height: 1;
    letter-spacing: 0.3px;
    color: var(--ink);
    text-transform: uppercase;
    white-space: nowrap;
  }
  .card__role {
    position: absolute;
    left: 445px;
    top: 160px;
    width: 505px;
    display: flex;
    align-items: center;
    gap: 10px;
    font-size: 20px;
    font-weight: 400;
    letter-spacing: 5px;
    color: var(--ink);
    white-space: nowrap;
  }
  .card__role::before,
  .card__role::after {
    content: "";
    flex: 1;
    height: 2px;
    background: var(--ink-soft);
  }
  .contact {
    position: absolute;
    left: 532px;
    width: 330px;
    text-align: center;
    color: var(--ink);
  }
  .contact__label {
    font-weight: 700;
    font-style: italic;
    font-size: 21px;
    line-height: 1;
  }
  .contact__value {
    margin-top: 10px;
    font-weight: 400;
    font-size: 29px;
    line-height: 1;
  }
  .contact--phone { top: 242px; }
  .contact--email { top: 350px; }
  .contact__divider {
    position: absolute;
    left: 532px;
    top: 327px;
    width: 330px;
    height: 1px;
    background: var(--rule);
  }
  .card__web {
    position: absolute;
    left: 470px;
    top: 466px;
    width: 440px;
    text-align: center;
    font-weight: 900;
    font-style: italic;
    font-size: 27px;
    letter-spacing: 2.5px;
    color: var(--ink);
    white-space: nowrap;
  }
</style>
</head>
<body>
<main class="canvas">
  <section class="card" aria-label="Business card front">
    <svg class="card__swoosh" viewBox="0 0 1000 647" aria-hidden="true">
      <defs>
        <linearGradient id="greyBand" x1="0" y1="0" x2="1" y2="0">
          <stop offset="0" stop-color="#cfcfcf"/>
          <stop offset="0.5" stop-color="#8e8e8e"/>
          <stop offset="1" stop-color="#d8d8d8"/>
        </linearGradient>
      </defs>
      <path d="M0,612 Q520,600 1000,478 L1000,647 L0,647 Z" fill="url(#greyBand)"/>
      <path d="M170,647 Q640,620 1000,468 L1000,647 Z" fill="var(--swoosh-black)"/>
    </svg>

    <div class="card__portrait" role="img" aria-label="Black and white portrait photo of the trainer with arms crossed"></div>

    <h1 class="card__name">Tobias Lendhart</h1>
    <p class="card__role">PERSONAL TRAINER</p>

    <div class="contact contact--phone">
      <p class="contact__label">Phone:</p>
      <p class="contact__value">0162/3819204</p>
    </div>
    <div class="contact__divider"></div>
    <div class="contact contact--email">
      <p class="contact__label">Email:</p>
      <p class="contact__value">info@yourmail.com</p>
    </div>

    <p class="card__web">www.YOURWEBSITE.com</p>
  </section>
</main>
</body>
</html>
```